Business Card Design (NEW FILES)

ATTENTION: New vector files are available. Please update your design to reflect/use the new (better resolution) logo images.

Seeking a unique and professional business card design for a commercial drone photography/videography business. The layout should feature
the logo (attached) and include the following information:
Owen Tarrick
614-502-7738
www.skylarkreelworks.example
NRD Certified Remote Pilot

Owen Tarrick

```html
<!DOCTYPE html>
<html lang="en">
<head>
<meta charset="utf-8">
<title>Skylark Reelworks – Business Card</title>
<link rel="stylesheet" href="https://fonts.googleapis.com/css2?family=Open+Sans:wght@400;600;700&display=swap">
<style>
  :root {
    --page: #232326;
    --navy: #1c1b4d;
    --orange: #ee8a4c;
    --white: #ffffff;
  }
  * { box-sizing: border-box; margin: 0; padding: 0; }
  html, body { width: 1200px; height: 780px; overflow: hidden; }
  body {
    background: var(--page);
    font-family: "Open Sans", Arial, sans-serif;
    display: flex;
    align-items: center;
    justify-content: center;
    gap: 40px;
  }
  .card {
    position: relative;
    width: 540px;
    height: 309px;
    background: var(--navy);
    color: var(--white);
    box-shadow: 0 18px 40px rgba(0,0,0,.55);
    overflow: hidden;
  }
  .edge-bar {
    position: absolute;
    width: 10px;
    background: var(--orange);
  }
  .edge-bar--right { right: 0; top: 40px; height: 120px; }
  .edge-bar--left { left: 0; bottom: 40px; height: 120px; }

  .brand {
    position: absolute;
    display: flex;
    align-items: center;
    gap: 12px;
    font-weight: 600;
    color: var(--white);
    letter-spacing: .04em;
    text-transform: uppercase;
    line-height: 1.05;
  }
  .brand__dot {
    flex: none;
    border-radius: 50%;
    background: var(--orange);
  }
  .card--front .brand {
    left: 0; right: 0; top: 0; bottom: 0;
    justify-content: center;
    font-size: 34px;
  }
  .card--front .brand__dot { width: 22px; height: 22px; }

  .card--back .brand {
    left: 40px; top: 150px;
    font-size: 20px;
  }
  .card--back .brand__dot { width: 14px; height: 14px; }

  .divider {
    position: absolute;
    left: 262px; top: 95px;
    width: 1.5px; height: 120px;
    background: var(--orange);
  }

  .contact {
    position: absolute;
    left: 290px; top: 58px;
  }
  .contact__name {
    font-size: 27px;
    font-weight: 700;
    line-height: 1.1;
  }
  .contact__first { color: var(--orange); }
  .contact__role {
    font-size: 12px;
    font-weight: 600;
    margin: 2px 0 14px 2px;
  }
  .contact__line {
    display: flex;
    align-items: center;
    gap: 8px;
    font-size: 12.5px;
    font-weight: 600;
    margin-bottom: 5px;
  }
  .contact__line svg { width: 12px; height: 12px; flex: none; }

  .credentials {
    position: absolute;
    left: 290px; top: 218px;
    width: 200px;
    text-align: center;
    font-size: 13px;
    font-weight: 600;
    line-height: 1.45;
  }
</style>
</head>
<body>

  <section class="card card--front">
    <span class="edge-bar edge-bar--right"></span>
    <span class="edge-bar edge-bar--left"></span>
    <div class="brand">
      <span class="brand__dot"></span>
      <span>Skylark<br>Reelworks</span>
    </div>
  </section>

  <section class="card card--back">
    <span class="edge-bar edge-bar--right"></span>
    <span class="edge-bar edge-bar--left"></span>

    <div class="brand">
      <span class="brand__dot"></span>
      <span>Skylark<br>Reelworks</span>
    </div>

    <span class="divider"></span>

    <div class="contact">
      <p class="contact__name"><span class="contact__first">Owen</span> Tarrick</p>
      <p class="contact__role">Owner</p>
      <p class="contact__line">
        <svg viewBox="0 0 24 24" aria-hidden="true"><path fill="#ee8a4c" d="M6.6 10.8a15.1 15.1 0 0 0 6.6 6.6l2.2-2.2a1 1 0 0 1 1-.25 11.4 11.4 0 0 0 3.6.57 1 1 0 0 1 1 1V20a1 1 0 0 1-1 1A17 17 0 0 1 3 4a1 1 0 0 1 1-1h3.5a1 1 0 0 1 1 1c0 1.25.2 2.45.57 3.6a1 1 0 0 1-.25 1z"/></svg>
        614-502-7738
      </p>
      <p class="contact__line">
        <svg viewBox="0 0 24 24" aria-hidden="true"><circle cx="12" cy="12" r="9.5" fill="none" stroke="#ee8a4c" stroke-width="2.5"/><path fill="none" stroke="#ee8a4c" stroke-width="2" d="M2.5 12h19M12 2.5c3 3 3 16 0 19M12 2.5c-3 3-3 16 0 19"/></svg>
        www.skylarkreelworks.example
      </p>
    </div>

    <p class="credentials">NRD Certified Remote Pilot<br>Fully Insured</p>
  </section>

</body>
</html>
```